Oak Ridge Ways Home Page

Redesign the home page -- make it look more attractive and inviting.
Do we need to cut down on the wording? Probably -
Want a cleaner design.
Can go to www.OakRidgeWays.org for the website

```html
<!DOCTYPE html>
<html lang="en">
<head>
<meta charset="utf-8">
<title>Oak Ridge Ways — Home</title>
<link href="https://fonts.googleapis.com/css2?family=Poppins:ital,wght@0,300;0,400;0,500;0,600;0,800;1,400&display=swap" rel="stylesheet">
<style>
:root{
  --blue:#2a44c8;
  --blue-dark:#1f36a8;
  --green:#21a540;
  --ink:#1d1f2e;
  --muted:#6d7080;
  --soft:#f2f3f6;
  --white:#ffffff;
}
*{box-sizing:border-box;margin:0;padding:0}
html,body{width:1200px;height:3834px;overflow:hidden}
body{position:relative;font-family:'Poppins',sans-serif;color:var(--ink);background:var(--white)}
.abs{position:absolute}

/* hero */
.hero{left:0;top:0;width:1200px;height:771px;background:linear-gradient(100deg,#2e2a1f 0%,#4a4030 35%,#7b6650 60%,#a58e78 80%,#6b5a48 100%)}
.hero-shade{left:0;top:0;width:1200px;height:771px;background:linear-gradient(90deg,rgba(0,0,0,.45),rgba(0,0,0,0) 60%)}
.nav-link{top:30px;font-size:13px;color:#fff}
.nav-link.active{color:#36d05a}
.brand{left:515px;top:18px;display:flex;align-items:center;gap:10px;color:#fff;font-size:19px;font-weight:500}
.brand-mark{width:36px;height:28px;background:var(--blue);border-radius:4px}
.phone-pill{left:721px;top:16px;width:175px;height:44px;border-radius:6px;background:var(--blue);color:#fff;font-size:14px;display:flex;align-items:center;justify-content:center;gap:10px}
.nav-util{top:30px;font-size:14px;color:#fff;display:flex;align-items:center;gap:7px}
.play{left:110px;top:216px;width:60px;height:60px;border-radius:50%;background:#fff}
.hero-eyebrow{left:110px;top:304px;font-size:17px;color:#fff}
.hero-title{left:110px;top:335px;font-size:44px;font-weight:800;color:#fff;letter-spacing:-.3px}
.hero-sub{left:110px;top:393px;font-size:36px;font-weight:300;color:#fff}
.hero-note{left:112px;top:455px;font-size:17px;color:#fff}
.scroll-cue{left:588px;top:694px}

/* buttons */
.btn{display:flex;align-items:center;height:48px;border-radius:6px;color:#fff;font-size:15px;font-weight:500;overflow:hidden;box-shadow:0 6px 14px rgba(0,0,0,.15)}
.btn .cap{width:48px;height:48px;border-radius:0 50% 50% 0;background:#151723;display:flex;align-items:center;justify-content:center;margin-right:12px}
.btn .txt{padding-right:20px}
.btn.blue{background:var(--blue)}
.btn.green{background:var(--green)}

/* packages */
.packages{left:0;top:771px;width:1200px;height:659px;background:var(--soft)}
.card{top:868px;width:345px;height:479px;background:#fff;border-radius:4px;box-shadow:0 10px 24px rgba(0,0,0,.08);text-align:center}
.card-head{height:82px;color:#fff;font-size:15px;line-height:29px;display:flex;align-items:center;justify-content:center;padding:0 30px;border-radius:4px 4px 0 0}
.card.silver .card-head{background:var(--blue)}
.card.gold .card-head{background:var(--green)}
.price{margin-top:32px;font-size:44px;font-weight:600;line-height:1}
.price small{font-size:16px;font-weight:400;color:var(--ink)}
.card.silver .price{color:var(--green)}
.card.gold .price{color:var(--blue)}
.get{margin-top:30px;font-size:21px}
.feat{list-style:none;margin-top:14px;font-size:12px;line-height:29px}
.feat li::before{content:"» ";color:var(--blue)}
.feat li.two{line-height:20px;padding:5px 40px}
.card .btn{position:absolute;left:68px;top:387px}
.card.gold .btn{left:68px}
.pk-title{left:859px;top:980px;width:235px;text-align:center;font-size:33px;font-weight:600;color:var(--blue)}
.pk-text{left:859px;top:1040px;width:235px;text-align:center;font-size:12.5px;line-height:26px;color:var(--muted)}

/* feature rows */
.feature h2{font-size:21px;font-weight:500;line-height:32px;color:var(--ink);width:500px}
.feature ul{list-style:none;margin-top:22px;width:500px}
.feature li{font-size:13.5px;line-height:27px;padding-left:20px;position:relative;margin-bottom:8px}
.feature li::before{content:"";position:absolute;left:2px;top:8px;width:11px;height:11px;border-radius:50%;border:3px solid var(--blue);box-sizing:border-box}
.quote{margin-top:20px;font-size:12.5px;font-style:italic;line-height:25px;color:var(--muted);width:490px}
.author{font-size:12.5px;font-weight:600;color:var(--blue);margin-top:2px}
.feature .btn{margin-top:34px;display:inline-flex}
.frame{border:1.5px solid #2a44c8;border-radius:10px 10px 0 0}
.photo{border-radius:18px 18px 18px 0;box-shadow:0 10px 22px rgba(0,0,0,.25)}
.side{font-size:13px;font-weight:600;letter-spacing:.5px;white-space:nowrap;transform-origin:left top;transform:rotate(-90deg)}
.side.blue{color:var(--blue)}
.side.green{color:var(--green)}
.side-line{width:2px;height:115px}

/* footer */
.footer{left:0;top:3563px;width:1200px;height:271px;background:var(--blue)}
.f-brand{left:112px;top:3627px;display:flex;align-items:center;gap:14px;color:#fff;font-size:30px;font-weight:500}
.f-mark{width:56px;height:50px;background:#fff;border-radius:4px}
.f-info{left:112px;color:#fff;font-size:16px;display:flex;align-items:center;gap:10px}
.f-links{left:724px;top:3631px;display:flex;gap:20px;color:#fff;font-size:15px}
.social{top:3680px;width:46px;height:46px;border-radius:50%;border:1.5px solid rgba(255,255,255,.8)}
.copy{left:893px;top:3752px;color:#fff;font-size:15px}
</style>
</head>
<body>

<!-- hero -->
<div class="abs hero" role="img" aria-label="Photo of a smiling young woman looking at her phone in a café"></div>
<div class="abs hero-shade"></div>
<span class="abs nav-link active" style="left:110px">Home</span>
<span class="abs nav-link" style="left:177px">Testimonials</span>
<span class="abs nav-link" style="left:288px">Max Scores</span>
<span class="abs nav-link" style="left:391px">FAQ</span>
<span class="abs nav-link" style="left:445px">Blog</span>
<div class="abs brand"><span class="brand-mark"></span>Oak Ridge Ways</div>
<div class="abs phone-pill">
  <svg width="20" height="20" viewBox="0 0 24 24"><path fill="#fff" d="M6.6 10.8a15 15 0 0 0 6.6 6.6l2.2-2.2c.3-.3.7-.4 1-.2 1.1.4 2.3.6 3.6.6.6 0 1 .4 1 1V20c0 .6-.4 1-1 1A17 17 0 0 1 3 4c0-.6.4-1 1-1h3.5c.6 0 1 .4 1 1 0 1.3.2 2.5.6 3.6.1.3 0 .7-.2 1z"/></svg>
  (555) 210-4478
</div>
<div class="abs nav-util" style="left:919px">
  <svg width="12" height="13" viewBox="0 0 12 13"><circle cx="6" cy="3.5" r="3" fill="#fff"/><path d="M0 13c0-4 2.5-5.5 6-5.5S12 9 12 13z" fill="#fff"/></svg>Login</div>
<div class="abs nav-util" style="left:1012px">
  <svg width="13" height="13" viewBox="0 0 13 13"><circle cx="5.5" cy="5.5" r="4" fill="none" stroke="#fff" stroke-width="2"/><path d="M8.5 8.5l3.5 3.5" stroke="#fff" stroke-width="2"/></svg>Search</div>

<div class="abs play"></div>
<svg class="abs" style="left:133px;top:231px" width="24" height="30" viewBox="0 0 24 30"><path d="M2 2l20 13L2 28z" fill="#1d1f2e"/></svg>
<div class="abs hero-eyebrow">Recognized as</div>
<div class="abs hero-title">The BEST Credit Score</div>
<div class="abs hero-sub">Improvement Program</div>
<div class="abs hero-note">81 Average Point Improvement</div>
<div class="abs btn blue" style="left:112px;top:507px"><span class="cap"><svg width="26" height="12" viewBox="0 0 26 12"><path d="M0 6h22M17 1l6 5-6 5" stroke="#fff" stroke-width="2.4" fill="none"/></svg></span><span class="txt">Get Started</span></div>
<svg class="abs scroll-cue" width="24" height="48" viewBox="0 0 24 48"><circle cx="12" cy="12" r="10" fill="#fff"/><circle cx="12" cy="11" r="3" fill="#1d1f2e"/><path d="M12 24v20M6 38l6 7 6-7" stroke="#21c04a" stroke-width="3" fill="none"/></svg>

<!-- packages -->
<div class="abs packages"></div>
<div class="abs card silver" style="left:112px">
  <div class="card-head">Silver: Lender's Report, Lender's Scores&amp; Analysis</div>
  <div class="price">$59.95<small>Only</small></div>
  <div class="get">Get Your</div>
  <ul class="feat">
    <li>Standard Credit Scores Lenders use</li>
    <li>Complete Credit Score Analysis</li>
    <li>Potential Mortgage and Auto Loan Qualifications</li>
  </ul>
  <div class="btn green"><span class="cap"><svg width="26" height="12" viewBox="0 0 26 12"><path d="M0 6h22M17 1l6 5-6 5" stroke="#fff" stroke-width="2.4" fill="none"/></svg></span><span class="txt">Get Started Here</span></div>
</div>
<div class="abs card gold" style="left:472px">
  <div class="card-head">Gold: Lender's Report, Lender's Scores, Analysis&amp; Steps to Score Improvement</div>
  <div class="price">$79.95<small>Only</small></div>
  <div class="get">Get Your</div>
  <ul class="feat">
    <li>Standard Credit Scores Lenders use</li>
    <li>Complete Credit Score Analysis</li>
    <li>Potential Mortgage and Auto Loan Qualifications</li>
    <li class="two">Personalized Solutions to Higher Standard Credit Scores</li>
  </ul>
  <div class="btn blue"><span class="cap"><svg width="26" height="12" viewBox="0 0 26 12"><path d="M0 6h22M17 1l6 5-6 5" stroke="#fff" stroke-width="2.4" fill="none"/></svg></span><span class="txt">Get Started Here</span></div>
</div>
<div class="abs pk-title">Our Packages</div>
<p class="abs pk-text">Lorem ipsum dolor sit amet, consectetur adipiscing elit, sed do eiusmod tempor incididunt ut labore et dolore magna aliqua. Ut enim ad minim veniam, quis nostrud exercitation ullamco laboris nisi ut aliquip ex ea commodo consequat.</p>

<!-- row 1 -->
<div class="abs frame" style="left:648px;top:1523px;width:422px;height:430px;border-right:none;border-top:1.5px solid #2a44c8"></div>
<div class="abs photo" style="left:664px;top:1533px;width:420px;height:447px;background:linear-gradient(135deg,#30343c,#1b2a3a 50%,#5a5f66)" role="img" aria-label="Photo of a laptop showing a credit score gauge"></div>
<div class="abs feature" style="left:110px;top:1556px">
  <h2>See What Your Lenders See - Get the Same Credit Report and Scores Lenders Use</h2>
  <ul>
    <li>As a Certified Credit Counselor, We Provide the Same Credit Report and 3 Scores Used by Mortgage &amp; Auto Lenders</li>
    <li>Don't be Misled by "Unreliable Internet Credit Scores" - Not Knowing Accurate Scores could Cost You Lots of Money</li>
  </ul>
  <p class="quote">I went to one of the credit bureau's websites and the score offered there was over 60 points higher than what my lender had my score at. I discovered my lender uses the same credit scores found here."</p>
  <div class="author">Owen R.</div>
  <div class="btn green"><span class="cap"><svg width="26" height="12" viewBox="0 0 26 12"><path d="M0 6h22M17 1l6 5-6 5" stroke="#fff" stroke-width="2.4" fill="none"/></svg></span><span class="txt">Learn More</span></div>
</div>
<div class="abs side-line" style="left:1131px;top:1570px;background:var(--blue)"></div>
<div class="abs side blue" style="left:1124px;top:1912px">SEE WHAT YOUR LENDERS SEE</div>

<!-- row 2 -->
<div class="abs frame" style="left:130px;top:2014px;width:430px;height:430px;border-left:none"></div>
<div class="abs photo" style="left:127px;top:2024px;width:420px;height:448px;background:linear-gradient(135deg,#6b5a48,#d8dde3 55%,#eef1f4)" role="img" aria-label="Photo of a credit report showing an excellent score beside glasses and a pen"></div>
<div class="abs feature" style="left:601px;top:2060px">
  <h2>Work with the BEST Credit Score Improvement Program</h2>
  <ul>
    <li>Oak Ridge Ways Averages an Amazing 81-Point Improvement for all 3 Standard Credit Scores</li>
    <li>Identifies Accounts to Pay Down (by Priority), to Close, to Use, to Open, to Refinance, and to Consolidate</li>
  </ul>
  <p class="quote">Oak Ridge Ways shows me a Road Map what to do! That's what we all need!"</p>
  <div class="author">Paul D.</div>
  <div class="btn blue"><span class="cap"><svg width="26" height="12" viewBox="0 0 26 12"><path d="M0 6h22M17 1l6 5-6 5" stroke="#fff" stroke-width="2.4" fill="none"/></svg></span><span class="txt">Learn More</span></div>
</div>
<div class="abs side-line" style="left:52px;top:2105px;background:var(--green)"></div>
<div class="abs side green" style="left:45px;top:2390px">WORK WITH THE BEST</div>

<!-- row 3 -->
<div class="abs frame" style="left:648px;top:2502px;width:422px;height:430px;border-right:none"></div>
<div class="abs photo" style="left:664px;top:2512px;width:420px;height:448px;background:linear-gradient(135deg,#7a8a70,#b9c1b3 45%,#e9ece8 60%,#9a7a62)" role="img" aria-label="Photo of hands holding a phone showing a finance approved message"></div>
<div class="abs feature" style="left:110px;top:2535px">
  <h2>Want to Know Your Potential Mortgage and Auto Loan Qualifications</h2>
  <ul>
    <li>Since We Provide the Same Standard Scores Lenders Use, We Give You Insight to Your Loan Qualifications</li>
    <li>See What Mortgage and Auto Loan Options Work Best for you. Don't Wait for a Loan Officer</li>
  </ul>
  <p class="quote">My score increased 110 points after 33 days (through Oak Ridge Ways). It is pretty cool and exciting to see my credit score(s) go up. I just bought my home."</p>
  <div class="author">Liam K.</div>
  <div class="btn green"><span class="cap"><svg width="26" height="12" viewBox="0 0 26 12"><path d="M0 6h22M17 1l6 5-6 5" stroke="#fff" stroke-width="2.4" fill="none"/></svg></span><span class="txt">Learn More</span></div>
</div>
<div class="abs side-line" style="left:1131px;top:2548px;background:var(--blue)"></div>
<div class="abs side blue" style="left:1124px;top:2925px">WANT TO KNOW YOUR POTENTIAL</div>

<!-- row 4 -->
<div class="abs frame" style="left:130px;top:3008px;width:430px;height:430px;border-left:none"></div>
<div class="abs photo" style="left:127px;top:3018px;width:420px;height:448px;background:linear-gradient(135deg,#2a2b30,#8d9096 45%,#dfe3ea 65%,#4f6db0)" role="img" aria-label="Photo of people reviewing financial charts with pens"></div>
<div class="abs feature" style="left:601px;top:3042px">
  <h2>Improve Your Purchasing Power by Increasing Your Lender's Standard Scores</h2>
  <ul>
    <li>Loan Officers Don't Care if You are Paying $100's More on Your Mortgage or Auto Loan Payment - You're Paying It!</li>
    <li>Most Home and Auto Buyers have Higher Payments because of Less-than-Excellent Standard Scores - Usually Less than 760</li>
  </ul>
  <p class="quote">"I am ready to buy my home. I will recommend this service to anyone needing help with credit. It is well worth the money."(Nora increased her score which improved her home purchasing power by 12.1%.)</p>
  <div class="author">Nora H.</div>
  <div class="btn blue"><span class="cap"><svg width="26" height="12" viewBox="0 0 26 12"><path d="M0 6h22M17 1l6 5-6 5" stroke="#fff" stroke-width="2.4" fill="none"/></svg></span><span class="txt">Learn More</span></div>
</div>
<div class="abs side-line" style="left:52px;top:3072px;background:var(--green)"></div>
<div class="abs side green" style="left:45px;top:3415px">IMPROVE YOUR PURCHASING</div>

<!-- footer -->
<div class="abs footer"></div>
<div class="abs f-brand"><span class="f-mark"></span>Oak Ridge Ways</div>
<div class="abs f-info" style="top:3695px;align-items:flex-start">
  <svg width="11" height="15" viewBox="0 0 11 15" style="margin-top:5px"><path d="M5.5 0A5.5 5.5 0 0 0 0 5.5C0 9.5 5.5 15 5.5 15S11 9.5 11 5.5A5.5 5.5 0 0 0 5.5 0zm0 7.5a2 2 0 1 1 0-4 2 2 0 0 1 0 4z" fill="#fff"/></svg>
  <span style="line-height:27px">118 Larkspur Avenue, Suite 210,<br>Millbrook, Oregon 97400</span>
</div>
<div class="abs f-info" style="top:3762px">
  <svg width="13" height="13" viewBox="0 0 24 24"><path fill="#fff" d="M6.6 10.8a15 15 0 0 0 6.6 6.6l2.2-2.2c.3-.3.7-.4 1-.2 1.1.4 2.3.6 3.6.6.6 0 1 .4 1 1V20c0 .6-.4 1-1 1A17 17 0 0 1 3 4c0-.6.4-1 1-1h3.5c.6 0 1 .4 1 1 0 1.3.2 2.5.6 3.6.1.3 0 .7-.2 1z"/></svg>
  (555) 210-4478
</div>
<div class="abs f-links"><span>Home</span><span>Testimonials</span><span>Max Scores</span><span>FAQ</span><span>Blog</span></div>
<div class="abs social" style="left:922px" aria-label="Professional network"></div>
<div class="abs social" style="left:979px" aria-label="Social page"></div>
<div class="abs social" style="left:1037px" aria-label="Photo sharing"></div>
<div class="abs copy">© 2022 All Rights Reserved</div>

</body>
</html>
```